Website Redesign using existing images, copy etc.

I'm looking for a website redesign/refresh of my current WordPress website. I would like to utilize the same photography, a new photo viewer, and an overall refresh of the entire design. This will need to be WordPress with simple accessibility to make changes as we add additional properties and make updates. We auction luxury real estate and luxury yachts for non-distressed sellers. It needs to be simple, luxurious and with ease of use for both web and especially mobile. www.BrindleHarrow.com

```html
<!DOCTYPE html>
<html lang="en">
<head>
<meta charset="utf-8">
<title>Brindle Harrow — Real Estate &amp; Yachts</title>
<link href="https://fonts.googleapis.com/css2?family=Josefin+Sans:wght@300;400;600;700&display=swap" rel="stylesheet">
<style>
:root{
  --gold:#a99a78;
  --gold-dark:#8f815f;
  --panel:#e6e6e6;
  --ink:#1a1a1a;
  --text:#333;
  --white:#fff;
  --footer:#0e0e0e;
}
*{margin:0;padding:0;box-sizing:border-box}
html,body{width:1200px;height:4208px;overflow:hidden}
body{position:relative;background:var(--white);font-family:'Josefin Sans',sans-serif;color:var(--text)}
.abs{position:absolute}
.btn{position:absolute;display:flex;align-items:center;justify-content:center;background:var(--gold);color:var(--white);border-radius:30px;font-weight:600;font-size:12px;letter-spacing:.5px;text-transform:uppercase}
.hero{left:0;top:0;width:1200px;height:600px;background:linear-gradient(180deg,#6d5a6e 0%,#b07f6c 22%,#a58a6a 38%,#4d5a3a 62%,#2f3b26 100%)}
.hero-curve{left:0;top:440px}
.ring{border:3px solid var(--white);border-radius:50%}
.nav{top:44px;left:500px;display:flex;gap:48px;color:var(--white);font-size:17px;font-weight:300;align-items:center}
.nav .phone{display:flex;align-items:center;gap:14px;margin-left:-8px}
.phone-dot{width:38px;height:38px;border-radius:50%;background:rgba(255,255,255,.25);display:flex;align-items:center;justify-content:center}
.hero-title{left:98px;top:180px;color:var(--white);font-size:56px;font-weight:300;letter-spacing:17px;display:flex;align-items:center;gap:26px;line-height:1}
.hero-sub{left:100px;top:282px;color:var(--white);font-size:27px;font-weight:400;letter-spacing:.5px}
.chev{left:569px;top:549px;width:62px;height:62px;border-radius:50%;background:var(--gold);display:flex;align-items:center;justify-content:center;box-shadow:0 3px 8px rgba(0,0,0,.2)}
.sec-title{width:1200px;text-align:center;color:var(--ink)}
.press-logos{top:780px;left:190px;width:820px;display:flex;justify-content:space-between;align-items:center}
.press-badge{background:#b4b4b4;border-radius:4px}
.lead{text-align:center;font-size:16.5px;font-weight:300;line-height:27.5px;color:var(--ink)}
.photo{position:absolute}
.panel{position:absolute;background:var(--panel)}
.panel h2{font-size:32px;font-weight:600;color:var(--ink);line-height:40px;letter-spacing:.5px}
.panel .kicker{color:var(--gold);font-size:17px;font-weight:400}
.panel p{font-size:14.5px;font-weight:300;line-height:28px;color:var(--ink)}
.card-img{position:absolute;width:322px;height:210px}
.card{position:absolute;width:296px;height:248px;background:var(--white);border-radius:20px 20px 30px 30px;box-shadow:0 8px 14px rgba(0,0,0,.12);padding:22px 18px 0 18px}
.card .row{display:flex;justify-content:space-between;align-items:center;font-size:13px;color:var(--ink)}
.pill{background:#e2e2e2;border-radius:14px;padding:6px 14px 4px;font-size:11px}
.card h3{font-size:21px;font-weight:600;color:var(--ink);line-height:31px;margin-top:18px;letter-spacing:.5px}
.card p{font-size:13.5px;font-weight:300;line-height:20px;color:var(--ink);margin-top:10px}
.card .btn{left:14px;bottom:14px;width:140px;height:42px;font-size:15px;font-weight:400;color:var(--ink)}
.foot{left:0;top:3720px;width:1200px;height:488px}
.foot-h{color:var(--white);font-size:21px;font-weight:600;letter-spacing:.5px}
.foot-links{color:var(--white);font-size:16px;font-weight:600;line-height:27.5px}
.contact-row{display:flex;gap:16px;color:var(--white);font-size:16px;line-height:23px}
.field{position:absolute;border:1px solid #fff;border-radius:7px;color:#fff;font-size:9px;font-weight:600;padding:10px 10px}
</style>
</head>
<body>

<div class="abs hero" role="img" aria-label="Photo of a Mediterranean-style luxury villa with palm trees under a dusk sky"></div>
<svg class="abs hero-curve" width="1200" height="180" viewBox="0 0 1200 180"><path d="M0 45 Q600 250 1200 45 L1200 180 L0 180 Z" fill="#fff"/></svg>

<div class="abs ring" style="left:99px;top:18px;width:72px;height:72px"></div>
<nav class="abs nav">
  <span>BUY</span><span>SELL</span><span>ABOUT</span><span>CONTACT</span>
  <span class="phone"><span class="phone-dot"><svg width="16" height="16" viewBox="0 0 24 24"><path fill="#fff" d="M6.6 10.8a15 15 0 0 0 6.6 6.6l2.2-2.2c.3-.3.7-.4 1-.2 1.1.4 2.3.6 3.6.6.6 0 1 .4 1 1V20c0 .6-.4 1-1 1C10.6 21 3 13.4 3 4c0-.6.4-1 1-1h3.5c.6 0 1 .4 1 1 0 1.3.2 2.5.6 3.6.1.3 0 .7-.2 1z"/></svg></span>+1 800-555-0142</span>
</nav>

<div class="abs hero-title"><span>BRINDLE</span><span class="ring" style="width:110px;height:110px;display:inline-block"></span><span>HARROW</span></div>
<div class="abs hero-sub">Real Estate &amp; Yachts</div>
<div class="btn" style="left:102px;top:349px;width:268px;height:52px">Browse Upcoming Auctions</div>
<div class="btn" style="left:386px;top:349px;width:230px;height:52px">Browse Past Successes</div>
<div class="abs chev"><svg width="24" height="24" viewBox="0 0 24 24" fill="none" stroke="#fff" stroke-width="2.4"><path d="M6 5l6 6 6-6M6 12l6 6 6-6"/></svg></div>

<div class="abs sec-title" style="top:707px;font-size:33px;font-weight:300">As Featured In</div>
<div class="abs press-logos">
  <div class="press-badge" style="width:100px;height:56px"></div>
  <div class="press-badge" style="width:118px;height:40px"></div>
  <div class="press-badge" style="width:126px;height:30px"></div>
  <div class="press-badge" style="width:132px;height:66px"></div>
  <div class="press-badge" style="width:62px;height:60px"></div>
</div>
<p class="abs lead" style="left:190px;top:886px;width:820px">By offering top-tier properties and vessels globally, along with strategic auction dates, exceptional marketing tactics, and a diligent public relations team, even the most prominent media outlets have taken notice. Check out some of our latest press features.</p>
<div class="btn" style="left:529px;top:1000px;width:142px;height:52px">View Press</div>

<div class="photo" style="left:98px;top:1127px;width:504px;height:412px;background:linear-gradient(160deg,#3a4a52 0%,#c59a78 35%,#e6e2dc 60%,#8b8176 100%)" role="img" aria-label="Photo of a covered veranda with wicker lounge chairs overlooking palms and the ocean at sunset"></div>
<div class="panel" style="left:491px;top:1250px;width:610px;height:338px;padding:26px 30px 0 34px">
  <h2>Over One Billion Dollars of<br>Auctions Marketed</h2>
  <div class="kicker" style="margin-top:14px">Real Estate &amp; Yachts</div>
  <p style="margin-top:26px">The experience of hearing the auctioneer’s final proclamation of “SOLD!” is unparalleled. Whether it’s the initial meeting with the seller at their estate or yacht, or the triumphant raising of the paddle by the winning buyer, we relish every moment of the process and the ensuing festivities. We’re confident that you will, too.</p>
</div>

<div class="abs" style="left:0;top:1860px;width:1200px;height:660px;background:linear-gradient(180deg,#ffffff 0%,#c5d6ee 14%,#8fb1de 30%,#f2f2f2 52%,#1b2a44 66%,#3f5f87 82%,#5d7ea8 100%)" role="img" aria-label="Photo of a navy-hulled luxury motor yacht on a marina with waterfront homes behind"></div>
<p class="abs lead" style="left:96px;top:1711px;width:1008px;font-size:15.5px;line-height:28.5px">Brindle Harrow is a top-tier destination for luxury property auctions, having overseen the auction marketing of numerous high-end estates and yachts. Our team of luxury home auction experts is committed to helping property owners obtain the best value for their assets while ensuring a timely sale. Whether you have an expansive compound or a metropolitan penthouse, Brindle Harrow has the necessary skills and expertise to facilitate various luxury real estate auctions. What’s even better? Our team takes care of every aspect of the process in cooperation with tour realtor/broker, including property tours, photography and cinematography, marketing advertising, public relations and more. Apart from high-end real estate auctions, we can also organize and execute luxury yacht auctions to help boat owners find qualified buyers for their vessels. Interested in finding out more about our luxury home and yacht auctions? Explore our current listings and success stories!</p>

<div class="photo" style="left:593px;top:2626px;width:503px;height:412px;background:linear-gradient(160deg,#6f8a5a 0%,#a7b59a 40%,#2f3e58 75%,#1f2b40 100%)" role="img" aria-label="Portrait photo of the company's CEO and founder in a navy blazer"></div>
<div class="panel" style="left:98px;top:2667px;width:610px;height:338px;padding:26px 24px 0 38px">
  <h2>About Us</h2>
  <div style="display:flex;align-items:center;gap:34px;margin-top:12px"><span class="kicker" style="font-size:20px;letter-spacing:1px">GORDON WELBY</span><span style="font-size:15px;color:var(--ink)">CEO &amp; FOUNDER</span></div>
  <p style="margin-top:20px;font-size:14.5px">Have you ever experienced a sense of purpose in your life? I consider myself fortunate enough to have felt it not once, but twice. At the age of 18, I realized my first calling as a Paratrooper in the US Army. Although I enjoyed being a Paratrooper, I knew it couldn’t last forever. After completing my service, I ventured</p>
  <div class="btn" style="left:38px;top:264px;width:140px;height:52px">View Press</div>
</div>
<div class="abs" style="left:115px;top:3025px;width:20px;height:20px;border-radius:50%;background:var(--gold)"></div>
<div class="abs" style="left:143px;top:3025px;width:20px;height:20px;border-radius:50%;border:1.5px solid var(--ink)"></div>

<div class="abs sec-title" style="top:3138px;font-size:31px;font-weight:600;letter-spacing:.5px">Upcoming Auctions</div>

<div class="card-img" style="left:98px;top:3217px;background:linear-gradient(180deg,#6f8f4e,#a39a7e 60%,#5a6b3c)" role="img" aria-label="Photo of a restored Victorian house among oak trees"></div>
<div class="card" style="left:111px;top:3380px">
  <div class="row"><span class="pill">AUG 12 2023</span><span></span></div>
  <h3>Charleston, SC | Under Contract</h3>
  <p>Beautifully restored 1870s-era Victorian in exclusive Harleston Village</p>
  <div class="btn">LEARN MORE</div>
</div>

<div class="card-img" style="left:439px;top:3217px;background:linear-gradient(180deg,#4f7a3f,#cfd6d0 55%,#4f7f48)" role="img" aria-label="Aerial photo of a white waterfront estate with pool and lawn"></div>
<div class="card" style="left:452px;top:3380px">
  <div class="row"><span class="pill">AUG 12 2023</span><span>Sold at Auction</span></div>
  <h3>Sarasota, FL | Sold</h3>
  <p style="margin-top:40px">Stunning, recently-remodeled waterfront estate near downtown</p>
  <div class="btn">LEARN MORE</div>
</div>

<div class="card-img" style="left:780px;top:3217px;background:linear-gradient(180deg,#8ab1d8,#7d9a58 45%,#2e6f8e 80%)" role="img" aria-label="Aerial photo of a marina with yachts in a green island harbour"></div>
<div class="card" style="left:793px;top:3380px">
  <div class="row"><span class="pill">AUG 12 2023</span><span>Accepting Offers</span></div>
  <h3>Corvel Cove Marina, St. Kitts</h3>
  <p style="margin-top:4px">Exclusive 200′ / 60m berth for vessels 170′ to 200′</p>
  <div class="btn">LEARN MORE</div>
</div>

<svg class="foot abs" viewBox="0 0 1200 488" width="1200" height="488"><path d="M0 86 Q600 -40 1200 86 L1200 488 L0 488 Z" fill="#0e0e0e"/></svg>

<div class="abs" style="left:101px;top:3841px;width:114px;height:114px;border-radius:50%;border:3px solid #fff"></div>
<div class="abs" style="left:101px;top:3972px;color:#fff;font-size:15px;font-weight:600;letter-spacing:.5px">Brindle Harrow</div>
<div class="abs" style="left:222px;top:3950px;width:90px;height:90px;border-radius:50%;background:#2a2720;border:6px solid #6b6250"></div>
<div class="abs" style="left:106px;top:4045px;width:32px;height:32px;border-radius:50%;background:#fff"></div>
<div class="abs" style="left:162px;top:4045px;width:32px;height:32px;border-radius:50%;background:#fff"></div>

<div class="abs foot-h" style="left:364px;top:3858px">USEFUL LINKS</div>
<div class="abs foot-links" style="left:365px;top:3906px">Home<br>Buy<br>Sell<br>About<br>Blog<br>Contact</div>

<div class="abs foot-h" style="left:591px;top:3858px">CONTACT US</div>
<div class="abs contact-row" style="left:591px;top:3906px;width:220px">
  <svg width="14" height="18" viewBox="0 0 24 30" style="flex:none;margin-top:2px"><path fill="#fff" d="M12 0C5.4 0 0 5.2 0 11.7 0 20 12 30 12 30s12-10 12-18.3C24 5.2 18.6 0 12 0zm0 16a4.5 4.5 0 1 1 0-9 4.5 4.5 0 0 1 0 9z"/></svg>
  <span>5010 Lorem ipsum dolor adipiscing 10018 US</span>
</div>
<div class="abs contact-row" style="left:591px;top:4004px">
  <svg width="14" height="14" viewBox="0 0 24 24" style="margin-top:2px"><path fill="#fff" d="M6.6 10.8a15 15 0 0 0 6.6 6.6l2.2-2.2c.3-.3.7-.4 1-.2 1.1.4 2.3.6 3.6.6.6 0 1 .4 1 1V20c0 .6-.4 1-1 1C10.6 21 3 13.4 3 4c0-.6.4-1 1-1h3.5c.6 0 1 .4 1 1 0 1.3.2 2.5.6 3.6.1.3 0 .7-.2 1z"/></svg>
  <span>+1 800-555-0142</span>
</div>
<div class="abs contact-row" style="left:591px;top:4050px;font-size:15px">
  <svg width="15" height="12" viewBox="0 0 24 18" style="margin-top:3px"><path fill="#fff" d="M0 0h24v18H0zM2 2v.5l10 7 10-7V2z"/></svg>
  <span>info@brindleharrow.com</span>
</div>

<div class="abs foot-h" style="left:849px;top:3858px">REQUEST A CALL BACK</div>
<div class="field" style="left:851px;top:3908px;width:118px;height:34px">NAME</div>
<div class="field" style="left:983px;top:3908px;width:118px;height:34px">EMAIL</div>
<div class="field" style="left:851px;top:3955px;width:250px;height:34px">PHONE</div>
<div class="field" style="left:851px;top:4004px;width:250px;height:90px">MESSAGES</div>
<div class="btn" style="left:856px;top:4110px;width:136px;height:40px;font-size:16px;font-weight:400;text-transform:none;color:var(--ink)">Submit</div>

<div class="abs" style="left:101px;top:4140px;color:#fff;font-size:16px;font-weight:600">© 2023 Brindle Harrow. All Rights Reserved.</div>
<div class="abs" style="left:470px;top:4140px;color:#fff;font-size:16px;font-weight:600">Privacy Policy</div>

</body>
</html>
```